New Business Card Design Project

We would like a business card that represents the sale of boat, home, auto, and life insurance.

The logo can change colors to meet the look of the design if needed.

Industry/Entity Type

Business

```html
<!DOCTYPE html>
<html lang="en">
<head>
<meta charset="utf-8">
<title>Crestline Financial – Business Card</title>
<link href="https://fonts.googleapis.com/css2?family=Jost:wght@400;500&family=Open+Sans:wght@400;600;700&display=swap" rel="stylesheet">
<style>
  :root {
    --page-bg: #e9ebec;
    --teal: #3b7287;
    --teal-text: #3c7f98;
    --white: #ffffff;
    --ink: #3a3a3a;
    --ink-soft: #555a5e;
    --card-shadow: 0 10px 30px rgba(0,0,0,.18);
  }
  * { box-sizing: border-box; margin: 0; padding: 0; }
  html, body { width: 1200px; height: 676px; overflow: hidden; }
  body {
    background: var(--page-bg);
    font-family: "Open Sans", Arial, sans-serif;
    position: relative;
  }
  .card {
    position: absolute;
    top: 188px;
    width: 520px;
    height: 300px;
    box-shadow: var(--card-shadow);
  }
  /* Front: teal side */
  .card-front {
    left: 70px;
    background: var(--teal);
    color: var(--white);
  }
  .front-brand {
    position: absolute;
    top: 62px;
    left: 0; right: 0;
    text-align: center;
  }
  .brand-mark {
    display: inline-flex;
    align-items: center;
    gap: 12px;
    font-family: "Open Sans", Arial, sans-serif;
    font-weight: 600;
    font-size: 34px;
    letter-spacing: 8px;
  }
  .brand-mark .dot {
    width: 18px; height: 18px; border-radius: 50%;
    background: currentColor;
  }
  .brand-sub {
    margin-top: 6px;
    font-family: "Jost", sans-serif;
    font-size: 26px;
    letter-spacing: 9px;
  }
  .brand-tagline {
    margin-top: 2px;
    font-family: "Jost", sans-serif;
    font-size: 17px;
    letter-spacing: 2.5px;
  }
  .front-contacts {
    position: absolute;
    left: 34px; right: 34px; bottom: 30px;
    display: flex;
    justify-content: space-between;
    font-size: 13px;
  }
  .contact-item { display: flex; align-items: center; gap: 7px; }
  .contact-icon {
    width: 16px; height: 16px; border-radius: 50%;
    border: 1px solid var(--white);
    font-size: 9px; line-height: 14px; text-align: center;
  }
  /* Back: white side */
  .card-back {
    left: 590px;
    background: var(--white);
    color: var(--ink);
  }
  .back-brand {
    position: absolute;
    top: 70px; left: 48px;
    display: flex; align-items: center; gap: 10px;
    color: var(--teal-text);
    font-weight: 700;
    font-size: 26px;
    letter-spacing: 3px;
  }
  .back-brand .dot {
    width: 16px; height: 16px; border-radius: 50%;
    background: currentColor;
  }
  .holder {
    position: absolute;
    top: 128px; left: 48px;
  }
  .holder-name {
    font-size: 22px;
    color: var(--ink);
    letter-spacing: .3px;
  }
  .holder-name .first { font-weight: 700; }
  .holder-name .role { font-size: 19px; }
  .holder-address {
    margin-top: 2px;
    font-size: 13px;
    color: var(--ink-soft);
  }
  .website {
    position: absolute;
    top: 210px; left: 48px;
    font-size: 18px;
    letter-spacing: 1px;
    color: var(--ink);
  }
  .website .domain { color: var(--teal-text); }
</style>
</head>
<body>
  <section class="card card-front">
    <div class="front-brand">
      <div class="brand-mark"><span class="dot"></span>CRESTLINE</div>
      <div class="brand-sub">financial</div>
      <div class="brand-tagline">investments &amp; insurance</div>
    </div>
    <div class="front-contacts">
      <div class="contact-item"><span class="contact-icon">T</span>01987654320</div>
      <div class="contact-item"><span class="contact-icon">F</span>01987654320</div>
      <div class="contact-item"><span class="contact-icon">E</span>hello@crestlinemail.com</div>
    </div>
  </section>

  <section class="card card-back">
    <div class="back-brand"><span class="dot"></span>CRESTLINE</div>
    <div class="holder">
      <div class="holder-name"><span class="first">NUWAN</span> SILVA <span class="role">/ PRESIDENT</span></div>
      <div class="holder-address">418/7 C, Palm Grove Road, Kadawatha Sri Lanka</div>
    </div>
    <div class="website">www.<span class="domain">crestlinecover</span>.com</div>
  </section>
</body>
</html>
```